BildeVOLD buisnesscard

Hey :) I need a modern buisnesscard for my company BildeVOLD
It most have:
Dagligleder og Fotograf: Henrik Audun Strandvik

Mob: +4791264085
Epost: post@bildevold.example
Adresse: Kvernbakken9, 6040 Langevåg

Facbook and instagram logo with text BildeVOLD

BildeVOLD logo

It Company

```html
<!DOCTYPE html>
<html lang="no">
<head>
<meta charset="utf-8">
<title>BildeVOLD – visittkort</title>
<link rel="stylesheet" href="https://fonts.googleapis.com/css2?family=Source+Sans+3:wght@400;600;700&display=swap">
<style>
  :root {
    --stage: #000000;
    --card: #2f3034;
    --card-edge: #36373b;
    --ink: #c4c4c6;
    --ink-soft: #d6d6d8;
    --mark: #b3b3b5;
    --rule: #3c3d41;
  }
  * { margin: 0; padding: 0; box-sizing: border-box; }
  html, body {
    width: 1200px; height: 900px; overflow: hidden;
    background: var(--stage);
    font-family: "Source Sans 3", "Myriad Pro", sans-serif;
  }
  .stage { position: relative; width: 1200px; height: 900px; }
  .card {
    position: absolute; top: 271px;
    width: 457px; height: 281px;
    border-radius: 14px;
    background: linear-gradient(180deg, var(--card-edge), var(--card));
  }
  .card--front { left: 137px; }
  .card--back { left: 626px; }

  .front-brand {
    position: absolute; left: 50px; top: 125px; width: 140px;
    text-align: center;
    font-weight: 700; font-size: 24px; color: var(--mark);
    letter-spacing: 0.2px;
  }
  .front-divider {
    position: absolute; left: 207px; top: 84px;
    width: 1px; height: 116px; background: var(--rule);
  }
  .details { position: absolute; left: 241px; top: 54px; color: var(--ink); }
  .details__name {
    font-size: 16.5px; font-weight: 600; color: var(--ink-soft);
    margin-bottom: 20px;
  }
  .contact { list-style: none; font-size: 13px; line-height: 19px; }
  .contact li { display: flex; align-items: center; gap: 7px; }
  .contact svg { width: 9px; height: 9px; fill: var(--ink); }
  .address { font-size: 13px; line-height: 20px; margin-top: 15px; }
  .social {
    display: flex; align-items: center; gap: 7px;
    margin-top: 13px; font-size: 13px; font-weight: 600; color: var(--ink-soft);
  }
  .social__dot { width: 15px; height: 15px; border-radius: 2px; background: var(--ink); }

  .back-brand {
    position: absolute; left: 0; right: 0; top: 72px;
    display: flex; flex-direction: column; align-items: center; gap: 14px;
  }
  .back-brand__square { width: 92px; height: 92px; background: var(--mark); }
  .back-brand__name {
    font-weight: 700; font-size: 42px; line-height: 1; color: var(--mark);
    letter-spacing: 0.5px;
  }
</style>
</head>
<body>
<main class="stage">
  <section class="card card--front" aria-label="Visittkort forside">
    <div class="front-brand">BildeVOLD</div>
    <div class="front-divider"></div>
    <div class="details">
      <p class="details__name">Henrik Audun Strandvik</p>
      <ul class="contact">
        <li>
          <svg viewBox="0 0 10 10" aria-hidden="true"><path d="M2 0.5 L3.6 2.6 L2.6 3.6 Q3.6 5.9 6.4 7.4 L7.4 6.4 L9.5 8 L8.4 9.5 Q1 8 0.5 1.6 Z"/></svg>
          <span>+4791264085</span>
        </li>
        <li>
          <svg viewBox="0 0 10 10" aria-hidden="true"><path d="M0 2 H10 V8.5 H0 Z M0.6 2.3 L5 5.6 L9.4 2.3" stroke="#2f3034" stroke-width="0.8"/></svg>
          <span>post@bildevold.example</span>
        </li>
      </ul>
      <p class="address">Kvernbakken9,<br>6040 Langevåg</p>
      <p class="social"><span class="social__dot"></span>BildeVOLD</p>
    </div>
  </section>

  <section class="card card--back" aria-label="Visittkort bakside">
    <div class="back-brand">
      <span class="back-brand__square"></span>
      <span class="back-brand__name">BildeVOLD</span>
    </div>
  </section>
</main>
</body>
</html>
```